Card design for orthopaedic surgeons working as The Brightwater Joint Centre

Business cards, letterhead

Colors

Designer to choose colors to be used in the design.

Requirements
Must have
• Late addition.
• Cards letterhead must have logos of
• Crestmoor Lindell College of Surgeons
• Varenwood Bone Health Association
Nice to have
• Back of card to have space for appointment time to be added by hand and some blank space for writing incidental other notes.

```html
<!DOCTYPE html>
<html lang="en">
<head>
<meta charset="utf-8">
<title>The Brightwater Joint Centre – Stationery</title>
<link rel="stylesheet" href="https://fonts.googleapis.com/css2?family=Roboto:wght@400;500;700&display=swap">
<style>
  :root {
    --backdrop: #c8c8c8;
    --paper: #ffffff;
    --navy: #022b45;
    --sky: #4aa3de;
    --ink: #1d2b3a;
    --crest-warm: #c9a24a;
    --crest-cool: #8fa3b5;
  }
  * { box-sizing: border-box; margin: 0; padding: 0; }
  html, body {
    width: 1200px; height: 763px; overflow: hidden;
    background: var(--backdrop);
    font-family: "Roboto", Arial, sans-serif;
    color: var(--ink);
  }
  .stage { position: relative; width: 1200px; height: 763px; }

  .wordmark { font-weight: 400; white-space: nowrap; color: var(--navy); letter-spacing: -0.2px; }

  .contact { list-style: none; }
  .contact li { display: flex; align-items: center; gap: 3px; }
  .contact svg { flex: none; }

  .badge { position: absolute; }

  /* Letterhead */
  .letterhead {
    position: absolute; left: 47px; top: 12px; width: 579px; height: 735px;
    background: var(--paper); overflow: hidden;
    box-shadow: 0 0 2px rgba(0,0,0,.25);
  }
  .letterhead .wordmark { position: absolute; left: 38px; top: 69px; font-size: 15px; }
  .letterhead .address { position: absolute; left: 417px; top: 36px; font-size: 8.4px; line-height: 11px; }
  .letterhead .contact { position: absolute; left: 417px; top: 60px; font-size: 8.6px; line-height: 12.6px; }
  .letterhead .badge-college { left: 47px; top: 629px; width: 56px; height: 72px; border-radius: 28px 28px 6px 6px; background: linear-gradient(var(--crest-warm), #b23a3a); }
  .letterhead .badge-association { left: 128px; top: 632px; width: 72px; height: 68px; border-radius: 6px; background: linear-gradient(var(--crest-cool), #e6e9ee); }
  .letterhead .sweep { position: absolute; left: 0; bottom: 0; width: 579px; height: 62px; }

  /* Business card common */
  .card {
    position: absolute; left: 659px; width: 442px; height: 254px;
    border-radius: 9px; overflow: hidden;
    box-shadow: 0 1px 3px rgba(0,0,0,.3);
  }
  .card-front { top: 114px; background: var(--paper); }
  .card-back { top: 401px; background: var(--navy); display: flex; align-items: center; justify-content: center; }

  .card-front .wordmark { position: absolute; left: 30px; top: 72px; font-size: 13px; }
  .card-front .badge-college { left: 33px; top: 107px; width: 68px; height: 88px; border-radius: 34px 34px 6px 6px; background: linear-gradient(var(--crest-warm), #b23a3a); }
  .card-front .badge-association { left: 130px; top: 110px; width: 90px; height: 82px; border-radius: 6px; background: linear-gradient(var(--crest-cool), #e6e9ee); }
  .card-front .divider { position: absolute; left: 238px; top: 66px; width: 1px; height: 123px; background: var(--sky); }
  .card-front .person { position: absolute; left: 254px; top: 63px; }
  .card-front .person-name { font-size: 14.4px; font-weight: 500; color: var(--sky); line-height: 18px; }
  .card-front .person-role { font-size: 11px; font-weight: 500; color: var(--ink); line-height: 14px; }
  .card-front .address { position: absolute; left: 254px; top: 106px; font-size: 10.5px; line-height: 14px; }
  .card-front .contact { position: absolute; left: 254px; top: 142px; font-size: 11.4px; line-height: 16px; }
  .card-front .sweep { position: absolute; left: 0; bottom: 0; width: 442px; height: 44px; }

  .card-back .wordmark { color: var(--paper); font-size: 25px; margin-top: -6px; }
</style>
</head>
<body>
<main class="stage">

  <section class="letterhead" aria-label="Letterhead">
    <div class="wordmark">The Brightwater Joint Centre</div>
    <address class="address" style="font-style:normal">48 Larkspur Ridge Road<br>Suite 310, Alderton, MI 48910</address>
    <ul class="contact">
      <li><svg width="9" height="9" viewBox="0 0 10 10"><path d="M2 1l2 2-1 1.3c.6 1.2 1.4 2 2.6 2.6L7 6l2 2-1.4 1.4C4.5 9 1 5.5.6 2.4z" fill="var(--sky)"/></svg>555 014 2290</li>
      <li><svg width="9" height="9" viewBox="0 0 10 10"><rect x="0.5" y="2" width="9" height="6" fill="var(--sky)"/><path d="M.5 2L5 5.5 9.5 2" stroke="#fff" fill="none"/></svg>info@brightwaterjoint.com</li>
      <li><svg width="9" height="9" viewBox="0 0 10 10" fill="none" stroke="var(--sky)"><circle cx="5" cy="5" r="4"/><ellipse cx="5" cy="5" rx="1.8" ry="4"/><path d="M1 5h8"/></svg>www.brightwaterjoint.com</li>
    </ul>
    <div class="badge badge-college" role="img" aria-label="Crestmoor Lindell College of Surgeons badge"></div>
    <div class="badge badge-association" role="img" aria-label="Varenwood Bone Health Association badge"></div>
    <svg class="sweep" viewBox="0 0 579 62" preserveAspectRatio="none" aria-hidden="true">
      <path d="M0 20 Q250 52 480 40 Q250 56 0 32Z" fill="var(--sky)"/>
      <path d="M0 32 Q270 58 579 4 L579 62 L0 62Z" fill="var(--navy)"/>
    </svg>
  </section>

  <section class="card card-front" aria-label="Business card front">
    <div class="wordmark">The Brightwater Joint Centre</div>
    <div class="badge badge-college" role="img" aria-label="Crestmoor Lindell College of Surgeons badge"></div>
    <div class="badge badge-association" role="img" aria-label="Varenwood Bone Health Association badge"></div>
    <div class="divider"></div>
    <div class="person">
      <div class="person-name">Daniel Hartwell</div>
      <div class="person-role">President</div>
    </div>
    <address class="address" style="font-style:normal">48 Larkspur Ridge Road<br>Suite 310, Alderton, MI 48910</address>
    <ul class="contact">
      <li><svg width="10" height="10" viewBox="0 0 10 10"><path d="M2 1l2 2-1 1.3c.6 1.2 1.4 2 2.6 2.6L7 6l2 2-1.4 1.4C4.5 9 1 5.5.6 2.4z" fill="var(--sky)"/></svg>555 014 2290</li>
      <li><svg width="10" height="10" viewBox="0 0 10 10"><rect x="0.5" y="2" width="9" height="6" fill="var(--sky)"/><path d="M.5 2L5 5.5 9.5 2" stroke="#fff" fill="none"/></svg>info@brightwaterjoint.com</li>
      <li><svg width="10" height="10" viewBox="0 0 10 10" fill="none" stroke="var(--sky)"><circle cx="5" cy="5" r="4"/><ellipse cx="5" cy="5" rx="1.8" ry="4"/><path d="M1 5h8"/></svg>www.brightwaterjoint.com</li>
    </ul>
    <svg class="sweep" viewBox="0 0 442 44" preserveAspectRatio="none" aria-hidden="true">
      <path d="M0 10 Q200 38 360 26 Q200 42 0 20Z" fill="var(--sky)"/>
      <path d="M0 20 Q220 46 442 0 L442 44 L0 44Z" fill="var(--navy)"/>
    </svg>
  </section>

  <section class="card card-back" aria-label="Business card back">
    <div class="wordmark">The Brightwater Joint Centre</div>
  </section>

</main>
</body>
</html>
```